Larkmoor Drones Business Card

We are a new company based in Central Queensland, Australia that uses specalised drones (Voskel Ferra Q80) to undertake mainly agricultural operations, like spraying weeds, spraying crops, spreading seed etc. I have attached a Plimbo proof of a card I was thinking along the lines of - purely a start point. The drone used in the business card MUST be a Voskel Ferra Q80.
I am very open to other ideas, especially fonts and layout. I don't have website etc set up yet.
The images are stock and easily interchangeable, I just ask that any background images reflect the local central Queensland area. The photo of the drone is not even complete (propellers cut off) and I need a new stock photo – I’m not sure if this is an issue, or I can pay for an image if need be. PLEASE FIND AN FERRA Q80 image - 4 sprayers, not 6.
The logo/business name is very draft and looking for further ideas, ideally incorporating drones or agriculture design elements into the design of the business name. The business name needs work on the graphic/design – it is a draft that I have included, the drone propellers (being a different colour) are DRAFT only and intended for changes. PLEASE DO NOT USE THE DRONE PORPELLER I HAVE USED AS A DRAFT. TRY TO FIND SOMETHING ELSE.. The arrow is a shape and not aligned in any way, I would also like ideas on different fonts and additional elements, like air streams, aviation elements, aviation or country western (farming like) themes and fonts etc.
Ideally looking at staying within the blue, green and yellow colours, keeping with an natural, outdoorsy, environmental feel.

Target Market(s)

Farmers, Agriculture, Local Governments, Land Managers

Industry/Entity Type

Agriculture, Drones, Aviation

Contact Information for Business Card

Agricultural Drone (Voskel Ferra Q80), Farming, Business Name.

Font styles to use
Sans Serif

Colors
0054AA
0677BA
7BADD7
CADEEF
E8F1F8
0094D4
00A9DD
6FCCEA
C7EBF8
E9F6FB
00AB8E
00BBA5
67D7C9
C6EFE9
E9F9F6
59FF00
82FF00
B8FF75
E3FFCB
F4FFEA

Requirements
Must have
• Voskel Ferra Q80 Drone
Should not have
• Tractors

```html
<!DOCTYPE html>
<html lang="en">
<head>
<meta charset="utf-8">
<title>Larkmoor Drones Business Card</title>
<link rel="stylesheet" href="https://fonts.googleapis.com/css2?family=Montserrat:ital,wght@0,600;0,700;0,800;1,800&family=Cinzel:wght@700&display=swap">
<style>
  :root {
    --slate: #4b5d78;
    --olive: #76902e;
    --ink: #1d1d1d;
    --rule: #8d93a0;
    --paper: #ffffff;
    --backdrop: #eeeeee;
    --photo-light: #e4e6e6;
    --photo-dark: #5c6062;
  }
  * { margin: 0; padding: 0; box-sizing: border-box; }
  html, body { width: 1200px; height: 1199px; overflow: hidden; background: var(--backdrop); }
  body { position: relative; font-family: "Montserrat", sans-serif; }

  .card {
    position: absolute;
    left: 258px;
    width: 684px;
    height: 390px;
    background: var(--paper);
    border: 1px solid #dcdcdc;
  }
  .card--front { top: 185px; }
  .card--back { top: 625px; }

  .wordmark {
    position: absolute;
    font-family: "Montserrat", sans-serif;
    font-weight: 800;
    color: var(--slate);
    text-transform: uppercase;
    text-align: center;
    line-height: 1.05;
  }
  .tagline {
    position: absolute;
    font-family: "Cinzel", serif;
    font-weight: 700;
    color: var(--ink);
    text-align: center;
    white-space: nowrap;
    letter-spacing: 0.5px;
  }

  .card--front .wordmark { left: 0; width: 684px; top: 124px; font-size: 40px; }
  .card--front .tagline { left: 0; width: 684px; top: 230px; font-size: 15px; }

  .card--back .wordmark { left: 58px; width: 243px; top: 32px; font-size: 28px; }
  .card--back .tagline { left: 58px; width: 243px; top: 104px; font-size: 11.5px; }

  .drone-photo {
    position: absolute;
    left: 40px; top: 142px;
    width: 286px; height: 100px;
    background: radial-gradient(ellipse at center, var(--photo-dark) 0%, #9a9d9e 35%, var(--photo-light) 70%, var(--paper) 100%);
  }

  .person { position: absolute; right: 36px; top: 170px; text-align: right; }
  .person__name { font-weight: 800; font-style: italic; font-size: 29px; color: var(--olive); line-height: 1.1; }
  .person__role { font-weight: 700; font-size: 17px; color: var(--slate); margin-top: 2px; }

  .divider { position: absolute; left: 36px; top: 274px; width: 614px; height: 2px; background: var(--rule); }

  .contact { position: absolute; left: 34px; top: 292px; list-style: none; }
  .contact li {
    display: flex; align-items: center; gap: 6px;
    font-weight: 600; font-size: 15px; color: var(--slate);
    height: 23px;
  }
  .contact svg { width: 15px; height: 15px; fill: var(--olive); flex: none; }

  .address {
    position: absolute; right: 36px; top: 294px;
    display: flex; align-items: center; gap: 8px;
  }
  .address p { font-weight: 700; font-size: 15px; line-height: 19px; color: var(--slate); text-align: right; text-transform: uppercase; }
  .address svg { width: 14px; height: 18px; fill: var(--olive); }
</style>
</head>
<body>

<section class="card card--front" aria-label="Business card front">
  <h1 class="wordmark">Larkmoor<br>Drones</h1>
  <p class="tagline">Servicing Central Queensland</p>
</section>

<section class="card card--back" aria-label="Business card back">
  <h2 class="wordmark">Larkmoor<br>Drones</h2>
  <p class="tagline">Servicing Central Queensland</p>

  <div class="drone-photo" role="img" aria-label="Photo of a Voskel Ferra Q80 agricultural spray drone in flight"></div>

  <div class="person">
    <p class="person__name">JOHN DOE</p>
    <p class="person__role">CEO &amp; FOUNDER</p>
  </div>

  <div class="divider"></div>

  <ul class="contact">
    <li>
      <svg viewBox="0 0 24 24" aria-hidden="true"><path d="M6.6 10.8a15.2 15.2 0 0 0 6.6 6.6l2.2-2.2c.3-.3.7-.4 1-.2 1.1.4 2.3.6 3.6.6.6 0 1 .4 1 1V20c0 .6-.4 1-1 1A17 17 0 0 1 3 4c0-.6.4-1 1-1h3.5c.6 0 1 .4 1 1 0 1.3.2 2.5.6 3.6.1.3 0 .7-.2 1z"/></svg>
      +61 7 4982 0316
    </li>
    <li>
      <svg viewBox="0 0 24 24" aria-hidden="true"><path d="M12 2a10 10 0 1 0 0 20 10 10 0 0 0 0-20zm6.9 6h-2.9a15.7 15.7 0 0 0-1.4-3.6A8 8 0 0 1 18.9 8zM12 4c.8 1.2 1.5 2.5 1.9 4h-3.8c.4-1.5 1.1-2.8 1.9-4zM4.3 14a8.2 8.2 0 0 1 0-4h3.4a16.5 16.5 0 0 0 0 4zm.8 2h2.9c.3 1.3.8 2.5 1.4 3.6A8 8 0 0 1 5.1 16zM8 8H5.1a8 8 0 0 1 4.3-3.6C8.8 5.5 8.3 6.7 8 8zm4 12c-.8-1.2-1.5-2.5-1.9-4h3.8c-.4 1.5-1.1 2.8-1.9 4zm2.3-6H9.7a14.7 14.7 0 0 1 0-4h4.6a14.7 14.7 0 0 1 0 4zm.3 5.6c.6-1.1 1.1-2.3 1.4-3.6h2.9a8 8 0 0 1-4.3 3.6zm1.7-5.6a16.5 16.5 0 0 0 0-4h3.4a8.2 8.2 0 0 1 0 4z"/></svg>
      LARKMOOR.COM
    </li>
    <li>
      <svg viewBox="0 0 24 24" aria-hidden="true"><path d="M6.6 10.8a15.2 15.2 0 0 0 6.6 6.6l2.2-2.2c.3-.3.7-.4 1-.2 1.1.4 2.3.6 3.6.6.6 0 1 .4 1 1V20c0 .6-.4 1-1 1A17 17 0 0 1 3 4c0-.6.4-1 1-1h3.5c.6 0 1 .4 1 1 0 1.3.2 2.5.6 3.6.1.3 0 .7-.2 1z"/></svg>
      EVAN.MARSH@LARKMOOR.COM
    </li>
  </ul>

  <div class="address">
    <p>118 Harlow Street,<br>Suite 4, Emerald, QLD<br>4720</p>
    <svg viewBox="0 0 16 22" aria-hidden="true"><path d="M8 0a8 8 0 0 0-8 8c0 6 8 14 8 14s8-8 8-14a8 8 0 0 0-8-8zm0 11a3 3 0 1 1 0-6 3 3 0 0 1 0 6z"/></svg>
  </div>
</section>

</body>
</html>
```